Building company buisness cards

We are looking for a sharp modern new look for our business cards.
We are a New Zealand based company that specialises in house and land packages.
We have attached a photo of the current logo and would like to see if it can be improved somehow if needed.
We are open to any colours but we have chosen green at this stage.
Feel free to change the font and make the logo smarter looking.
Play with the colours and see what looks best.

We want a card that looks so good know one will want to throw it away!

Target Market(s)

Home buyers

Industry/Entity Type

Building

Contact Information for Business Card

Derek Tolvane
0217394062
dtolvane@quillmarkhomesteads.co.nz
quillmarkhomesteads.co.nz

Font styles to use
Serif
Sans Serif

Colors

Designer to choose colors to be used in the design.

Requirements
Must have
• Logo and company name on one side, details on the other side
Nice to have
• Color codes for the original green are HEX #4a8028, RGB(74,128,40), CMYK(42,0,69,50)
• Round corners, Raised and/or spot UV

```html
<!DOCTYPE html>
<html lang="en">
<head>
<meta charset="utf-8">
<title>Quillmark Homesteads – Business Cards</title>
<link href="https://fonts.googleapis.com/css2?family=Tinos:wght@400;700&display=swap" rel="stylesheet">
<style>
  :root {
    --canvas-bg: #e9e7e3;
    --card-white: #ffffff;
    --card-black: #0d0d0d;
    --brand-green: #1fb83a;
    --band-green: #2cbf3f;
    --rule-grey: #c9c9c9;
    --text-white: #f4f4f4;
    --text-dark: #141414;
  }
  * { margin: 0; padding: 0; box-sizing: border-box; }
  html, body {
    width: 1200px;
    height: 1024px;
    overflow: hidden;
    background: var(--canvas-bg);
  }
  .canvas {
    width: 1200px;
    height: 1024px;
    display: flex;
    flex-direction: column;
    align-items: center;
    justify-content: center;
    gap: 28px;
  }
  .card {
    position: relative;
    width: 840px;
    height: 470px;
    border-radius: 16px;
    overflow: hidden;
    background: var(--card-white);
    box-shadow: 0 6px 22px rgba(0,0,0,0.14);
  }

  /* Front: company name side */
  .card-front {
    display: flex;
    flex-direction: column;
    align-items: center;
    justify-content: center;
  }
  .brand {
    display: flex;
    align-items: center;
    gap: 18px;
  }
  .brand-square {
    width: 30px;
    height: 30px;
    background: var(--brand-green);
    flex: none;
  }
  .brand-name {
    font-family: "Tinos", serif;
    font-weight: 700;
    font-size: 52px;
    color: var(--brand-green);
    line-height: 1;
    white-space: nowrap;
  }
  .brand-rule {
    width: 120px;
    height: 2px;
    background: var(--rule-grey);
    margin-top: 30px;
  }

  /* Back: details side */
  .card-back .house-shape {
    position: absolute;
    inset: 0;
  }
  .details {
    position: absolute;
    left: 64px;
    top: 236px;
    font-family: "Tinos", serif;
  }
  .person-name {
    font-weight: 700;
    font-size: 42px;
    color: var(--brand-green);
    margin-bottom: 18px;
  }
  .contact-line {
    display: flex;
    align-items: center;
    gap: 14px;
    font-size: 27px;
    color: var(--text-white);
    line-height: 1.25;
  }
  .contact-icon {
    width: 22px;
    height: 22px;
    flex: none;
  }
  .email-band {
    position: absolute;
    left: 0;
    right: 0;
    bottom: 0;
    height: 72px;
    background: var(--band-green);
    display: flex;
    align-items: center;
    padding-left: 64px;
    font-family: "Tinos", serif;
    font-size: 27px;
    color: var(--text-dark);
  }
</style>
</head>
<body>
<main class="canvas">

  <section class="card card-front" aria-label="Card front">
    <div class="brand">
      <span class="brand-square"></span>
      <h1 class="brand-name">Quillmark Homesteads</h1>
    </div>
    <div class="brand-rule"></div>
  </section>

  <section class="card card-back" aria-label="Card back">
    <svg class="house-shape" width="840" height="470" viewBox="0 0 840 470" aria-hidden="true">
      <polygon points="0,210 470,210 600,70 730,210 840,210 840,470 0,470" fill="var(--card-black)"/>
      <polyline points="462,210 600,62 738,210" fill="none" stroke="var(--brand-green)" stroke-width="16" stroke-linejoin="round"/>
    </svg>

    <div class="details">
      <p class="person-name">Derek Tolvane</p>
      <p class="contact-line">
        <svg class="contact-icon" viewBox="0 0 22 22" aria-hidden="true">
          <rect width="22" height="22" rx="3" fill="var(--brand-green)"/>
          <path d="M7 5 L9.5 5 L10.5 8 L9 9.2 C9.8 11 11 12.2 12.8 13 L14 11.5 L17 12.5 L17 15 C17 16 16 17 15 17 C10 16.5 5.5 12 5 7 C5 6 6 5 7 5 Z" fill="var(--card-black)"/>
        </svg>
        0217394062
      </p>
      <p class="contact-line">
        <svg class="contact-icon" viewBox="0 0 22 22" aria-hidden="true">
          <rect width="22" height="22" rx="3" fill="var(--brand-green)"/>
          <circle cx="11" cy="11" r="6" fill="none" stroke="var(--card-black)" stroke-width="1.6"/>
          <line x1="5" y1="11" x2="17" y2="11" stroke="var(--card-black)" stroke-width="1.4"/>
          <ellipse cx="11" cy="11" rx="2.6" ry="6" fill="none" stroke="var(--card-black)" stroke-width="1.4"/>
        </svg>
        quillmarkhomesteads.co.nz
      </p>
    </div>

    <div class="email-band">dtolvane@quillmarkhomesteads.co.nz</div>
  </section>

</main>
</body>
</html>
```